Meridale Real Estate

We are looking for help with web design for a new company that is revolutionizing the real estate world on the listing side: by charing per hour for top level professional real estate services. We would like the concept to be simple, clean and easily understood.
Updates

We want this website to actually function, not just a static design.

Industry/Entity Type

Real Estate

```html
<!DOCTYPE html>
<html lang="en">
<head>
<meta charset="utf-8">
<title>Meridale Real Estate</title>
<link href="https://fonts.googleapis.com/css2?family=Open+Sans:wght@400;600;700&display=swap" rel="stylesheet">
<style>
:root{
  --black:#000;
  --accent:#29a9e0;
  --accent-light:#5bc0f0;
  --text:#6b6b6b;
  --text-dark:#222;
  --panel:#f3f3f3;
  --line:#d9d9d9;
  --footer:#2b2b2b;
  --footer-text:#c9c9c9;
  --white:#fff;
}
*{margin:0;padding:0;box-sizing:border-box}
html,body{width:1007px;height:1200px;overflow:hidden;background:var(--white)}
body{position:relative;font-family:"Open Sans",Arial,sans-serif;color:var(--text)}
a{color:inherit;text-decoration:none}

.site-header{position:absolute;left:0;top:0;width:1007px;height:587px;background:var(--black)}
.brand{position:absolute;left:158px;top:38px;width:200px;display:flex;align-items:center;gap:12px;color:var(--white);font-size:14px;font-weight:600;letter-spacing:3px;line-height:20px;text-transform:uppercase}
.brand-mark{flex:none;width:24px;height:24px;border:2px solid var(--white);border-radius:50%}
.brand-name{display:block}

.main-nav{position:absolute;top:45px;left:0;width:1007px;height:27px}
.main-nav a{position:absolute;top:0;height:27px;line-height:27px;font-size:13.5px;color:var(--white);text-transform:uppercase;white-space:nowrap}
.main-nav a.is-active{background:var(--accent);font-weight:600;padding:0 10px}

.hero{position:absolute;left:84px;top:120px;width:840px;height:444px;overflow:hidden}
.hero-photo{position:absolute;inset:0;background:linear-gradient(180deg,#27405f 0%,#3c5a7a 25%,#8a6a3e 55%,#c99449 72%,#6b4a25 88%,#1e3d52 100%)}
.hero-prev{position:absolute;left:12px;top:207px;width:27px;height:27px;border-radius:50%;background:rgba(255,255,255,.85)}
.hero-caption{position:absolute;left:24px;top:383px;width:544px;height:43px;background:rgba(0,0,0,.65);color:var(--white);font-size:22px;font-weight:600;line-height:43px;padding-left:12px;letter-spacing:.3px;text-transform:uppercase;white-space:nowrap}

.property-search{position:absolute;left:671px;top:137px;width:237px;height:411px;background:rgba(10,22,34,.82);padding:0 18px}
.property-search h2{margin-top:12px;text-align:center;color:var(--accent-light);font-size:19.5px;font-weight:600;line-height:27px;text-transform:uppercase;letter-spacing:.3px}
.field{margin-top:10px}
.field + .field{margin-top:10.5px}
.field label{display:block;color:#c5ccd2;font-size:13px;line-height:16px;margin-bottom:5px}
.select{position:relative;height:30px;background:var(--white);border-radius:2px;color:#999;font-size:12.5px;line-height:30px;padding-left:11px}
.select svg{position:absolute;right:9px;top:12px}
.search-btn{display:block;margin:17px auto 0;width:106px;height:29px;background:#d8d8d8;border:0;border-radius:2px;font-family:inherit;font-weight:600;font-size:13.5px;color:#333;text-transform:uppercase}

.intro{position:absolute;left:100px;top:615px;width:807px;text-align:center;font-size:14px;line-height:21px;color:#777}

.listings{position:absolute;left:84px;top:730px;width:840px;height:251px;background:var(--panel);border-top:1px solid var(--line);border-bottom:1px solid var(--line)}
.listings h2{position:absolute;left:13px;top:16px;color:var(--accent);font-size:16.5px;font-weight:700;text-transform:uppercase}
.listings-next{position:absolute;right:11px;top:19px}
.listing-card{position:absolute;top:51px;width:151px;height:184px;background:var(--white);border:1px solid #ddd;text-align:center}
.listing-photo{margin:7px auto 0;width:135px;height:107px}
.listing-card h3{margin-top:8px;font-size:12.5px;font-weight:600;color:var(--text-dark)}
.listing-card p{font-size:12px;line-height:16px;color:#777}

.contacts{position:absolute;left:0;top:1017px;width:1007px;height:99px;border-top:1px solid var(--line);background:linear-gradient(180deg,#fff 0%,#fff 60%,#eeeeee 100%)}
.contact{position:absolute;top:16px;font-size:12px;line-height:17.5px;color:#666;white-space:nowrap}
.contact .name{color:var(--accent)}
.contact-icon{position:absolute;left:-30px;top:3px}

.site-footer{position:absolute;left:0;top:1116px;width:1007px;height:84px;background:var(--footer)}
.footer-nav{position:absolute;left:85px;top:19px;font-size:11.5px;color:var(--footer-text)}
.footer-nav span{margin:0 10px}
.copyright{position:absolute;left:85px;top:50px;font-size:7.5px;font-weight:700;color:var(--white)}
.social{position:absolute;top:1147px;width:21px;height:21px;border-radius:50%;background:#6f6f6f}
.social svg{position:absolute;left:5px;top:6px}
</style>
</head>
<body>

<header class="site-header">
  <a class="brand" href="#"><span class="brand-mark"></span><span class="brand-name">Meridale<br>Real Estate</span></a>
  <nav class="main-nav">
    <a class="is-active" href="#" style="left:384px">Home</a>
    <a href="#" style="left:463px">Commercial</a>
    <a href="#" style="left:576px">Residential</a>
    <a href="#" style="left:684px">Farm</a>
    <a href="#" style="left:749px">Vacant Land</a>
    <a href="#" style="left:866px">Contact</a>
  </nav>

  <section class="hero">
    <div class="hero-photo" role="img" aria-label="Modern white two-storey house with lit glass walls and a covered patio beside a pool at dusk"></div>
    <span class="hero-prev">
      <svg width="27" height="27" viewBox="0 0 27 27"><path d="M15 9l-5 4.5 5 4.5" fill="none" stroke="#999" stroke-width="1.5"/></svg>
    </span>
    <div class="hero-caption">Commercial &amp; Residential Representation</div>
  </section>

  <form class="property-search">
    <h2>Property Search</h2>
    <div class="field"><label>Property For</label><div class="select">Buy<svg width="10" height="6"><path d="M0 0h10L5 6z" fill="#999"/></svg></div></div>
    <div class="field"><label>Price range</label><div class="select">$0 - $10000<svg width="10" height="6"><path d="M0 0h10L5 6z" fill="#999"/></svg></div></div>
    <div class="field"><label>Category</label><div class="select">Any<svg width="10" height="6"><path d="M0 0h10L5 6z" fill="#999"/></svg></div></div>
    <div class="field"><label>Country</label><div class="select">Any<svg width="10" height="6"><path d="M0 0h10L5 6z" fill="#999"/></svg></div></div>
    <div class="field"><label>City</label><div class="select">Any<svg width="10" height="6"><path d="M0 0h10L5 6z" fill="#999"/></svg></div></div>
    <button class="search-btn" type="button">Search Now</button>
  </form>
</header>

<p class="intro">Curabitur aliquet auctor consectetur. Suspendisse pharetra imperdiet nulla quis auctor. Sed at urna eu diam fringilla mattis. Praesent ac metus id odio interdum ornare. Aenean pulvinar, elit a ornare ullamcorper, metus mauris suscipit nisi, id tincidunt risus lorem luctus sem. Nulla in dolor vel lacus lacinia consequat eu at nunc. Integer tristique pretium purus, non vehicula eros consequat eu. Donec sed felis eget leo ullamcorper porttitor.</p>

<section class="listings">
  <h2>Latest Listings</h2>
  <svg class="listings-next" width="15" height="15" viewBox="0 0 15 15"><circle cx="7.5" cy="7.5" r="7.5" fill="#c8c8c8"/><path d="M6 4.5l3.5 3-3.5 3z" fill="#fff"/></svg>

  <article class="listing-card" style="left:12px">
    <div class="listing-photo" role="img" aria-label="Bright white open-plan living room with wooden floor" style="background:linear-gradient(180deg,#e6e4e1,#c8c2ba 60%,#7c6a58)"></div>
    <h3>Phasellus in diam</h3><p>Grand Cayman<br>Cayman Islands</p>
  </article>
  <article class="listing-card" style="left:178px">
    <div class="listing-photo" role="img" aria-label="Two-storey stone family house with front lawn" style="background:linear-gradient(180deg,#c9d6e2,#a08a72 45%,#7a6a55 75%,#5f7d3e)"></div>
    <h3>Phasellus in diam</h3><p>Grand Cayman<br>Cayman Islands</p>
  </article>
  <article class="listing-card" style="left:345px">
    <div class="listing-photo" role="img" aria-label="Yellow beachfront villa with palm trees" style="background:linear-gradient(180deg,#ffffff,#e8d79a 45%,#4f7a3c 75%,#8aa6b8)"></div>
    <h3>Phasellus in diam</h3><p>Grand Cayman<br>Cayman Islands</p>
  </article>
  <article class="listing-card" style="left:511px">
    <div class="listing-photo" role="img" aria-label="Modern house with infinity pool at dusk" style="background:linear-gradient(180deg,#2b3140,#5b5560 40%,#8a6f7e 65%,#3f7fb0)"></div>
    <h3>Phasellus in diam</h3><p>Grand Cayman<br>Cayman Islands</p>
  </article>
  <article class="listing-card" style="left:678px">
    <div class="listing-photo" role="img" aria-label="Sunny living room with sofas and large windows" style="background:linear-gradient(180deg,#eef0ef,#d8d2c6 55%,#8a6d52)"></div>
    <h3>Phasellus in diam</h3><p>Grand Cayman<br>Cayman Islands</p>
  </article>
</section>

<section class="contacts">
  <div class="contact" style="left:183px">
    <svg class="contact-icon" width="18" height="20" viewBox="0 0 18 20"><rect x="1" y="1" width="16" height="18" fill="#888"/><rect x="4" y="4" width="4" height="12" fill="#fff"/><rect x="10" y="4" width="4" height="12" fill="#fff"/></svg>
    PROPERTIES BY HALDEN<br>1875 Orchard Ridge Lane<br>Millbrook, CA 95011<br>BRE#04471209
  </div>
  <div class="contact" style="left:446px">
    <svg class="contact-icon" width="18" height="20" viewBox="0 0 18 20"><rect x="1" y="1" width="16" height="18" fill="#888"/><rect x="4" y="4" width="4" height="12" fill="#fff"/><rect x="10" y="4" width="4" height="12" fill="#fff"/></svg>
    <span class="name">Dana M. Corwell</span><br>dana@haldenprops.com<br>(555) 014-2290<br>BRE#03328140
  </div>
  <div class="contact" style="left:700px">
    <svg class="contact-icon" width="18" height="20" viewBox="0 0 18 20"><rect x="1" y="1" width="16" height="18" fill="#888"/><rect x="4" y="4" width="4" height="12" fill="#fff"/><rect x="10" y="4" width="4" height="12" fill="#fff"/></svg>
    <span class="name">Owen T. Barlow</span><br>&nbsp;owen@haldenprops.com<br>555.018.4471 &nbsp;- &nbsp;555.019.3360<br>BRE#02650817
  </div>
</section>

<footer class="site-footer">
  <nav class="footer-nav">
    <a href="#">Home</a><span>|</span><a href="#">Commercial</a><span>|</span><a href="#">Residential</a><span>|</span><a href="#">Farm</a><span>|</span><a href="#">Vacant land</a><span>|</span><a href="#">Contact</a>
  </nav>
  <p class="copyright">© Copyrights 2015 Meridale Real Estate. All Right Reserved</p>
</footer>

<a class="social" href="#" style="left:815px" aria-label="Social profile"></a>
<a class="social" href="#" style="left:844px" aria-label="Social profile"></a>
<a class="social" href="#" style="left:874px" aria-label="Social profile"></a>
<a class="social" href="#" style="left:903px" aria-label="Email">
  <svg width="11" height="9" viewBox="0 0 11 9"><rect x=".5" y=".5" width="10" height="8" fill="none" stroke="#2b2b2b"/><path d="M.5 .5l5 4 5-4" fill="none" stroke="#2b2b2b"/></svg>
</a>

</body>
</html>
```